Help design website for "Brightwater Civic Advisors" to advance the common good

Here is the Google doc link that lays out the design:

https://files.plumrivet.example/sheet/d/7QmTzR2wLx9KpVbN4hJcY8sEaUoFdG3iXkMnPq5rWt6/edit?usp=sharing

Here is the Google drive folder with the logos and photos: https://vault.plumrivet.example/open?id=4HkWp9LzQe2TxRvN8mBaYc3DsUoJfG6

The testimonials are being gathered and will be shared by Friday, 1/4.

The winner will also have to migrate the coding files to my hosting site.

Thank you for your help! Looking forward to seeing your designs.

Target Market(s)

Prospective clients

Industry/Entity Type

Non Profit

Coding

Coded - Design and coding required

Number of Pages Required

5+ page

Requirements
Must have
• Noted in the Google doc regarding layout.
Nice to have

```html
<!DOCTYPE html>
<html lang="en">
<head>
<meta charset="utf-8">
<title>Brightwater Civic Advisors</title>
<link href="https://fonts.googleapis.com/css2?family=Poppins:wght@400;500;600;700&display=swap" rel="stylesheet">
<style>
:root{
  --bg-slate:#33343e;
  --bg-charcoal:#2c2c2d;
  --text-white:#ffffff;
  --text-muted:#b9bac2;
  --text-dim:#8c8d96;
  --accent:#4aa8e8;
  --field:#3c3d46;
  --field-line:#4a4b54;
}
*{margin:0;padding:0;box-sizing:border-box}
html,body{width:1200px;height:3679px;overflow:hidden}
body{font-family:"Poppins",sans-serif;color:var(--text-white);background:var(--bg-slate);position:relative}
section,header,footer{position:absolute;left:0;width:1200px}
.abs{position:absolute}
.title{position:absolute;left:0;width:1200px;text-align:center;font-weight:600;font-size:30px}
.rule{position:absolute;left:570px;width:60px;height:3px;background:var(--accent)}
.lead{position:absolute;left:340px;width:520px;text-align:center;font-size:10.5px;line-height:17px;color:var(--text-muted)}
.btn{position:absolute;background:var(--accent);color:#fff;font-size:12px;font-weight:500;display:flex;align-items:center;justify-content:center;border-radius:3px}

/* header */
.hero{top:0;height:515px;background:var(--bg-slate)}
.brand{left:233px;top:28px;display:flex;align-items:center;gap:10px}
.brand-mark{width:30px;height:30px;background:var(--accent)}
.brand-name{font-size:15px;font-weight:500;line-height:18px;width:150px;letter-spacing:.5px}
.nav{left:586px;top:38px;display:flex;gap:20px;font-size:11px;font-weight:500}
.nav .active{color:var(--accent);border-bottom:2px solid var(--accent);padding-bottom:3px}
.portrait{left:160px;top:125px;width:430px;height:390px;border-radius:215px 215px 0 0;background:radial-gradient(circle at 50% 40%,#6b5c55 0%,#3b3638 55%,#2b2b31 100%)}
.hero-name{left:628px;top:190px;font-size:46px;font-weight:600}
.hero-sub{left:628px;top:255px;width:260px;font-size:13px;line-height:18px;color:#e6e7ec}

/* about */
.about{top:515px;height:405px;background:var(--bg-charcoal)}
.about-ring{left:305px;top:100px;width:100px;height:100px;border:6px solid #4a4336;border-radius:50%}
.about-title{left:302px;top:186px;font-size:28px;font-weight:600}
.about-rule{left:318px;top:228px;width:86px;height:3px;background:var(--accent)}
.about-copy{left:510px;top:38px;width:450px;font-size:9.5px;line-height:15px;color:var(--text-muted)}
.about-copy p{margin-bottom:12px}

/* services */
.services{top:920px;height:933px;background:var(--bg-slate)}
.card{position:absolute;width:354px;height:199px;border-radius:6px;padding:26px 18px}
.card h3{font-size:13.5px;font-weight:600;margin-bottom:12px}
.card p{font-size:9.5px;line-height:15px;color:rgba(255,255,255,.85)}
.c1{background:linear-gradient(135deg,#1fc1dc,#1a97d6)}
.c2{background:linear-gradient(135deg,#2bd6a3,#1bb8b7)}
.c3{background:linear-gradient(135deg,#f2d62a,#deb22d)}
.c4{background:linear-gradient(135deg,#f1864a,#e0352e)}
.c5{background:linear-gradient(135deg,#38dc8a,#29c9a4)}
.c6{background:linear-gradient(135deg,#3489e4,#1f5ed2)}

/* gallery */
.gallery{top:1853px;height:859px;background:var(--bg-charcoal)}
.tabs{left:0;width:1200px;top:214px;display:flex;justify-content:center;gap:22px;font-size:10px;color:var(--text-muted)}
.tabs .on{color:var(--accent);border-bottom:2px solid var(--accent);padding-bottom:3px}
.photo{position:absolute}
.p-warm{background:linear-gradient(160deg,#7a5c4a,#3d3431)}
.p-hall{background:linear-gradient(160deg,#a8846a,#4d3a30)}
.p-stage{background:linear-gradient(160deg,#8a7460,#5a4a3e)}
.p-room{background:linear-gradient(160deg,#8c5a3c,#4a3326)}
.p-table{background:linear-gradient(160deg,#9b6a4c,#5b4a46)}
.p-group{background:linear-gradient(160deg,#6d5a50,#332c2a)}
.p-bright{background:linear-gradient(160deg,#c19a6b,#55402f)}
.p-lake{background:linear-gradient(180deg,#cfe1ef 0%,#9fbfd6 45%,#4b5a6a 100%)}

/* work history */
.work{top:2712px;height:270px;background:var(--bg-slate)}
.work-title{font-weight:700;letter-spacing:.5px}
.arrow{position:absolute;top:172px;width:22px;height:22px;border-radius:50%;background:#3b8fd3;display:flex;align-items:center;justify-content:center}
.client{position:absolute;top:140px;height:81px;background:#fff;display:flex;align-items:center;justify-content:center;text-align:center;color:#2c2c2d;font-size:12px;font-weight:600;line-height:15px;padding:0 6px}

/* contact */
.contact{top:2982px;height:576px;background:var(--bg-charcoal)}
.info-head{left:235px;font-size:12px;font-weight:500}
.info{left:235px;display:flex;gap:12px;font-size:9.5px;line-height:14px;color:var(--text-muted)}
.info svg{flex:none;margin-top:1px}
.social{left:235px;top:398px;display:flex;gap:12px}
.social span{width:8px;height:8px;border-radius:50%;background:var(--text-dim)}
.label{font-size:8.5px;color:var(--text-dim);letter-spacing:.5px}
.field{position:absolute;background:var(--field);border:1px solid var(--field-line);border-radius:2px;font-size:9.5px;color:var(--text-dim);padding:0 12px;display:flex;align-items:center}
.field.area{align-items:flex-start;padding-top:12px}

/* footer */
.footer{top:3558px;height:121px;background:var(--bg-slate)}
.footer-name{top:30px;left:0;width:1200px;text-align:center;font-size:14px;font-weight:500}
.footer-note{top:96px;left:0;width:1200px;text-align:center;font-size:9px;color:var(--text-muted)}
</style>
</head>
<body>

<header class="hero">
  <div class="abs brand">
    <span class="brand-mark"></span>
    <span class="brand-name">BRIGHTWATER CIVIC ADVISORS</span>
  </div>
  <nav class="abs nav">
    <span class="active">Home</span><span>About</span><span>Services</span><span>Gallery</span><span>Testimonials</span><span>Media</span><span>Contact</span>
  </nav>
  <div class="abs portrait" role="img" aria-label="Portrait photo of the founder, Mara Lindqvist"></div>
  <h1 class="abs hero-name">I’m Mara</h1>
  <p class="abs hero-sub">Lorem ipsum dolor sit amet esta di maria nun seo valencia</p>
  <div class="btn" style="left:628px;top:395px;width:142px;height:39px">Contact Me</div>
</header>

<section class="about">
  <div class="abs about-ring"></div>
  <h2 class="abs about-title">About Me</h2>
  <div class="abs about-rule"></div>
  <div class="abs about-copy">
    <p>Brightwater Civic Advisors supports nonprofit organizations and educational institutions to carry out their missions to benefit the wider community.</p>
    <p>Founder Mara Lindqvist is an educator with a 22-year record of demonstrated achievement and leadership roles in nonprofit and educational institutions. Most recently, she served as Associate Dean of Students in the University and Director of the Campus Civic Service Center at Lakeshore University. Mara has designed, implemented, and evaluated community-based learning and leadership training programs that have obtained positive outcomes documented by survey results, recognition by outside agencies, and grants awarded for new initiatives and expansions. She has also significantly and consistently increased the number of program applicants, volunteers, and community partnerships through innovative programming, improved reputation, targeted recruitment, marketing and communications.</p>
    <p>Mara is a native Midwesterner and has also lived in Osaka, Portland, Denver, and Baltimore. Mara received her bachelor of arts from Northfield Ridge College and her masters in education from Eastbay Graduate School.</p>
  </div>
  <div class="btn" style="left:510px;top:324px;width:123px;height:40px">View Works</div>
</section>

<section class="services">
  <h2 class="title" style="top:56px">Services</h2>
  <div class="rule" style="top:104px"></div>
  <p class="lead" style="top:128px">Excepteur sint occaecat cupidatat non proident, sunt in culpa qui officia deserunt mollit anim id est laborum. Sed ut perspiciatis unde omnis iste natur.</p>

  <div class="card c1" style="left:235px;top:214px"><h3>Staff Professional Development</h3><p>Mara has supervised, coached, and mentored hundreds of staff members, including professionals and students. She uses the “scaffold model coach-lead” approach to empower and guide her staff in their personal and professional growth. She has led professional development workshops and staff retreats.</p></div>
  <div class="card c2" style="left:609px;top:214px"><h3>Community Partnership Development</h3><p>Mara has collaborated with more than 250 nonprofits, schools, government agencies, and businesses with corporate social responsibility aims to create mutually beneficial partnerships. These relationships have been strengthened and sustained to expand programming and initiatives that meet community engagement outcomes.</p></div>
  <div class="card c3" style="left:235px;top:432px"><h3>Group Facilitation &amp; Leadership Training</h3><p>Mara has facilitated diverse groups, experiential learning activities, and dialogues on social justice issues, such as power and privilege, education, and poverty. She has developed curriculum and lesson plans for students to gain essential civic leadership competencies.</p></div>
  <div class="card c4" style="left:609px;top:432px"><h3>Program Design, Implementation, &amp; Evaluation</h3><p>Mara has launched several programs that take into account best practices, as well as particular institutional cultures, participant demographics, and geographical location. The evaluation data of these programs have demonstrated their impact, and she has secured funding and developed key partnerships for program expansion.</p></div>
  <div class="card c5" style="left:235px;top:651px"><h3>Event Planning</h3><p>Mara has planned events of all sizes that bring together students, staff, faculty, alumni, community partners, leaders and residents for dialogue and service.</p></div>
  <div class="card c6" style="left:609px;top:651px"><h3>Strategic Planning</h3><p>At Lakeshore University, Mara established and managed a 16-member Advisory Board, including undergraduates, graduate students, faculty, campus colleagues, community partners, and alumni. She has also served on nonprofit and higher education boards to inform their strategic priorities, goals, and the allocation of funding and resources.</p></div>
</section>

<section class="gallery">
  <h2 class="title" style="top:44px">Gallery</h2>
  <div class="rule" style="top:92px"></div>
  <p class="lead" style="top:130px">Excepteur sint occaecat cupidatat non proident, sunt in culpa qui officia deserunt mollit anim id est laborum. Sed ut perspiciatis unde omnis iste natur.</p>
  <div class="abs tabs"><span class="on">All</span><span>Image Cat 1</span><span>Image Cat 2</span><span>Image Cat 3</span><span>Image Cat 4</span><span>Image Cat5</span></div>

  <div class="photo p-warm" style="left:235px;top:260px;width:354px;height:361px" role="img" aria-label="Photo of a smiling student group at an outdoor event"></div>
  <div class="photo p-hall" style="left:609px;top:260px;width:169px;height:174px" role="img" aria-label="Photo of a message wall in a hallway"></div>
  <div class="photo p-stage" style="left:797px;top:260px;width:167px;height:174px" role="img" aria-label="Photo of a speaker at a podium"></div>
  <div class="photo p-room" style="left:609px;top:451px;width:169px;height:170px" role="img" aria-label="Photo of a crowded reception room"></div>
  <div class="photo p-table" style="left:797px;top:451px;width:167px;height:170px" role="img" aria-label="Photo of a workshop around a table"></div>
  <div class="photo p-group" style="left:235px;top:643px;width:169px;height:169px" role="img" aria-label="Photo of a small group at an evening gathering"></div>
  <div class="photo p-bright" style="left:422px;top:643px;width:167px;height:169px" role="img" aria-label="Photo of volunteers holding up signs"></div>
  <div class="photo p-lake" style="left:609px;top:643px;width:355px;height:169px" role="img" aria-label="Photo of a large group by a lakeshore"></div>
</section>

<section class="work">
  <h2 class="title work-title" style="top:38px">WORK HISTORY</h2>
  <div class="rule" style="top:86px"></div>
  <div class="arrow" style="left:188px"><svg width="8" height="10" viewBox="0 0 8 10"><path d="M6 1 2 5l4 4" stroke="#fff" stroke-width="2" fill="none"/></svg></div>
  <div class="arrow" style="left:990px"><svg width="8" height="10" viewBox="0 0 8 10"><path d="M2 1l4 4-4 4" stroke="#fff" stroke-width="2" fill="none"/></svg></div>
  <div class="client" style="left:233px;width:140px">Campus Civic Service Center</div>
  <div class="client" style="left:383px;width:76px">Cardinal Fellows</div>
  <div class="client" style="left:466px;width:201px">Harbor Bay Schools</div>
  <div class="client" style="left:677px;width:88px">ServeNation</div>
  <div class="client" style="left:775px;width:190px">Civic Learners</div>
</section>

<section class="contact">
  <h2 class="title" style="top:60px">Contact Me</h2>
  <div class="rule" style="top:108px"></div>

  <div class="abs info-head" style="top:150px">Contact Info</div>
  <div class="abs info" style="top:195px"><svg width="10" height="12" viewBox="0 0 10 12"><path d="M5 0a4 4 0 0 1 4 4c0 3-4 8-4 8S1 7 1 4a4 4 0 0 1 4-4z" fill="#8c8d96"/><circle cx="5" cy="4" r="1.5" fill="#2c2c2d"/></svg><span>2040 Alder Ave, Springfield, USA</span></div>
  <div class="abs info" style="top:235px"><svg width="12" height="10" viewBox="0 0 12 10"><rect width="12" height="10" rx="1" fill="#8c8d96"/><path d="M0 1l6 4 6-4" stroke="#2c2c2d" fill="none"/></svg><span>hello@brightwatercivic.example</span></div>
  <div class="abs info" style="top:275px"><svg width="11" height="11" viewBox="0 0 11 11"><path d="M2 0h2l1 3-1.5 1a6 6 0 0 0 3.5 3.5L8 6l3 1v2a2 2 0 0 1-2 2A9 9 0 0 1 0 2a2 2 0 0 1 2-2z" fill="#8c8d96"/></svg><span>+1 555 014 2280<br>+1 555 014 2291</span></div>
  <div class="abs info" style="top:328px"><svg width="11" height="11" viewBox="0 0 11 11"><circle cx="5.5" cy="5.5" r="5" fill="none" stroke="#8c8d96"/><path d="M0.5 5.5h10M5.5 0.5c-3 3-3 7 0 10M5.5 0.5c3 3 3 7 0 10" stroke="#8c8d96" fill="none"/></svg><span>www.brightwatercivic.example</span></div>
  <div class="abs info-head" style="top:370px;font-size:11px">Follow Me</div>
  <div class="abs social"><span></span><span></span><span></span><span></span><span></span></div>

  <div class="abs label" style="left:486px;top:148px">NAME</div>
  <div class="field" style="left:486px;top:171px;width:483px;height:35px">Type your name</div>
  <div class="abs label" style="left:486px;top:226px">PHONE NUMBER</div>
  <div class="field" style="left:486px;top:252px;width:231px;height:35px">Type your phone number</div>
  <div class="abs label" style="left:736px;top:226px">EMAIL</div>
  <div class="field" style="left:736px;top:252px;width:233px;height:35px">Type your email address</div>
  <div class="abs label" style="left:486px;top:310px">YOUR MESSAGE</div>
  <div class="field area" style="left:486px;top:331px;width:483px;height:123px">Type your message here</div>
  <div class="btn" style="left:486px;top:480px;width:125px;height:40px">Send Message</div>
</section>

<footer class="footer">
  <div class="abs footer-name">Brightwater Civic Advisors</div>
  <div class="abs footer-note">All Rights Reserved, 2019, Brightwater Civic Advisors</div>
</footer>

</body>
</html>
```